Fernhale Business Card Design

We are looking for a fresh business card design for our new logo. We would like a business card that is unique but friendly. We are in the window coverings business offering blinds, shutters and shades for homes.

Target Market(s)

Targeting the end-consumer

Industry/Entity Type

Business

Requirements
Must have
• Must have a dedicates space for a photo of our sales person. Must contain our new logo (attached).

```html
<!DOCTYPE html>
<html lang="en">
<head>
<meta charset="utf-8">
<title>Fernhale Business Card</title>
<link rel="stylesheet" href="https://fonts.googleapis.com/css2?family=Lora:wght@500&family=Oswald:wght@500&family=Work+Sans:wght@400;500&display=swap">
<style>
  :root {
    --backdrop: #1c1c1c;
    --card: #1f2021;
    --card-edge: #2a2b2c;
    --silver: #d9d9d9;
    --muted: #8a8b8c;
    --emboss: #121313;
    --emboss-text: #5c5d5f;
    --divider: #5a5b5c;
    --photo: #2e2f31;
    --photo-ring: #3c3d3f;
  }
  * { margin: 0; padding: 0; box-sizing: border-box; }
  html, body {
    width: 1200px;
    height: 900px;
    overflow: hidden;
    background: radial-gradient(ellipse at 50% 40%, #2c2c2c 0%, var(--backdrop) 70%);
  }
  .stage {
    width: 1200px;
    height: 900px;
    display: flex;
    flex-direction: column;
    align-items: center;
    justify-content: center;
    gap: 40px;
  }
  .card {
    position: relative;
    width: 620px;
    height: 354px;
    background: linear-gradient(135deg, var(--card-edge) 0%, var(--card) 55%, #1a1b1c 100%);
    box-shadow: 0 14px 30px rgba(0, 0, 0, 0.55);
  }
  /* Front */
  .brand {
    position: absolute;
    left: 0; right: 0; top: 120px;
    display: flex;
    align-items: center;
    justify-content: center;
    gap: 20px;
  }
  .brand-mark {
    width: 52px;
    height: 52px;
    border: 2px solid var(--emboss);
    border-radius: 8px;
  }
  .brand-name {
    font-family: "Lora", serif;
    font-weight: 500;
    font-size: 58px;
    color: var(--silver);
    letter-spacing: 1px;
  }
  .front-url {
    position: absolute;
    left: 0; right: 0; bottom: 34px;
    text-align: center;
    font-family: "Work Sans", sans-serif;
    font-size: 14px;
    letter-spacing: 2px;
    color: var(--muted);
  }
  /* Back */
  .photo {
    position: absolute;
    left: 34px; top: 100px;
    width: 96px; height: 96px;
    border-radius: 50%;
    background: radial-gradient(circle at 40% 35%, #38393b 0%, var(--photo) 70%);
    border: 2px solid var(--photo-ring);
  }
  .person {
    position: absolute;
    left: 138px; top: 108px;
    width: 174px;
    text-align: right;
  }
  .person-name {
    font-family: "Oswald", sans-serif;
    font-weight: 500;
    font-size: 30px;
    line-height: 1.2;
    letter-spacing: 1px;
    color: var(--emboss-text);
    text-shadow: 0 -1px 0 #0c0c0d, 0 1px 0 #3a3b3c;
    text-transform: uppercase;
    white-space: nowrap;
  }
  .person-role {
    font-family: "Work Sans", sans-serif;
    font-size: 13px;
    letter-spacing: 2px;
    color: var(--emboss-text);
    text-shadow: 0 -1px 0 #0c0c0d;
    text-transform: uppercase;
    white-space: nowrap;
  }
  .divider {
    position: absolute;
    left: 326px; top: 98px;
    width: 1px; height: 100px;
    background: var(--divider);
  }
  .contacts {
    position: absolute;
    left: 342px; top: 112px;
    list-style: none;
    display: flex;
    flex-direction: column;
    gap: 8px;
  }
  .contact {
    display: flex;
    align-items: center;
    gap: 12px;
    font-family: "Work Sans", sans-serif;
    font-size: 14px;
    letter-spacing: 0.5px;
    color: var(--silver);
    white-space: nowrap;
  }
  .contact svg { width: 14px; height: 14px; flex: none; fill: none; stroke: var(--muted); stroke-width: 1.6; }
  .address {
    position: absolute;
    left: 40px; bottom: 40px;
    font-family: "Work Sans", sans-serif;
    font-size: 15px;
    letter-spacing: 1px;
    color: var(--emboss-text);
    text-shadow: 0 -1px 0 #0c0c0d;
  }
</style>
</head>
<body>
<main class="stage">
  <section class="card card-front">
    <div class="brand">
      <span class="brand-mark"></span>
      <span class="brand-name">Fernhale</span>
    </div>
    <p class="front-url">www.fernhalehome.com</p>
  </section>

  <section class="card card-back">
    <div class="photo" role="img" aria-label="Photo of the sales person"></div>
    <div class="person">
      <p class="person-name">Daniel Reid</p>
      <p class="person-role">Sales Manager</p>
    </div>
    <span class="divider"></span>
    <ul class="contacts">
      <li class="contact">
        <svg viewBox="0 0 16 16"><path d="M3 2h3l1.5 3.5-2 1.2a8 8 0 0 0 3.8 3.8l1.2-2L14 10v3a1 1 0 0 1-1 1A12 12 0 0 1 2 3a1 1 0 0 1 1-1z"/></svg>
        +44 (0)1632 960418
      </li>
      <li class="contact">
        <svg viewBox="0 0 16 16"><rect x="1.5" y="3.5" width="13" height="9"/><path d="M1.5 3.5 8 9l6.5-5.5"/></svg>
        amyfarrow@fernhaleblinds.com
      </li>
      <li class="contact">
        <svg viewBox="0 0 16 16"><circle cx="8" cy="8" r="6.5"/><path d="M1.5 8h13M8 1.5c-3 3.5-3 9.5 0 13M8 1.5c3 3.5 3 9.5 0 13"/></svg>
        www.fernhaleblinds.com
      </li>
    </ul>
    <p class="address">18 Mill Lane Ayrshire, Scotland KA99 2ZZ</p>
  </section>
</main>
</body>
</html>
```